US company needs luxury product packaging design for a line of hair extensions

What we Need:
Design product packaging for our top of the line hair extension product called Verosina™, the design should have the Verosina™ name,and the head from our Dovetress logo on the box.

Who we are
Our company DoveTress™ is a wholesaler of 100% human hair extensions. We sell the best quality double drawn hair wefts, clip-ins and wigs.

The detailed brief is in the attached word document with examples of packaging we like and we have also uploaded our company logo

The winning designer(s) will work with us on 9 other products packages that we need, so it is important to think strategically

Thanks

Target Market(s)

African American Women

Industry/Entity Type

Hair And Beauty

Font styles to use
Serif
Decorative
Script

Colors
fbf289
b768aa
e24096
000000
fbd4d5
f59195
ffc214
d3a5cc
eda3c7

Requirements
Must have
• Evoke luxury
Nice to have
• See Attached brief

```html
<!DOCTYPE html>
<html lang="en">
<head>
<meta charset="utf-8">
<title>Verosina — Hair Care Instructions</title>
<link rel="stylesheet" href="https://fonts.googleapis.com/css2?family=Nunito+Sans:wght@400;600&display=swap">
<style>
  :root {
    --paper: #ffffff;
    --panel: #000000;
    --ink: #ffffff;
    --gold-light: #f7dc86;
    --gold-mid: #e2b54f;
    --gold-deep: #a9792a;
  }
  html, body {
    margin: 0;
    padding: 0;
    width: 739px;
    height: 1200px;
    overflow: hidden;
    background: var(--paper);
  }
  .card {
    position: relative;
    width: 739px;
    height: 1200px;
    font-family: "Nunito Sans", sans-serif;
  }
  .card__panel {
    position: absolute;
    left: 0;
    top: 0;
    width: 739px;
    height: 1200px;
  }
  .brand-name {
    position: absolute;
    left: 98px;
    top: 318px;
    margin: 0;
    font-family: "Nunito Sans", sans-serif;
    font-weight: 600;
    font-size: 70px;
    letter-spacing: 1px;
    color: var(--gold-mid);
    line-height: 1;
  }
  .care {
    position: absolute;
    left: 94px;
    top: 474px;
    width: 580px;
    color: var(--ink);
  }
  .care__title {
    margin: 0 0 22px;
    font-weight: 600;
    font-size: 33px;
    line-height: 1.2;
  }
  .care__steps {
    list-style: none;
    margin: 0;
    padding: 0;
    font-weight: 400;
    font-size: 28.5px;
    line-height: 36.5px;
  }
  .care__step {
    padding-left: 39px;
    text-indent: -39px;
    margin-bottom: 16px;
  }
</style>
</head>
<body>
<main class="card">
  <svg class="card__panel" viewBox="0 0 739 1200" aria-hidden="true">
    <defs>
      <linearGradient id="goldBand" x1="0" y1="0" x2="1" y2="0">
        <stop offset="0" stop-color="var(--gold-light)" stop-color-fallback="#f7dc86"/>
        <stop offset="0.45" stop-color="#c8963a"/>
        <stop offset="0.75" stop-color="#a9792a"/>
        <stop offset="1" stop-color="#f4d57a"/>
      </linearGradient>
    </defs>
    <path class="panel-body"
          d="M41 204 C 200 150, 330 190, 430 260 C 520 320, 610 360, 697 346 L 697 1162 L 41 1162 Z"
          fill="#000000"/>
    <path class="panel-band"
          d="M41 188 C 200 130, 330 170, 430 240 C 520 302, 610 342, 697 330 L 697 352 C 610 366, 520 326, 430 264 C 330 194, 200 156, 41 210 Z"
          fill="url(#goldBand)"/>
  </svg>

  <p class="brand-name">Verosina</p>

  <section class="care">
    <h1 class="care__title">Hair Care Instructions:</h1>
    <ol class="care__steps">
      <li class="care__step">1. When brushing Verosina, start at<br>the ends and methodically work<br>up towards the root using a weave<br>brush</li>
      <li class="care__step">2. Shampoo hair using a mild<br>moisturizing shampoo</li>
      <li class="care__step">3. After shampooing, rinse hair<br>thoroughly with warm water and<br>condition with your favorite<br>conditioner</li>
      <li class="care__step">4. Blow dry or use any type dryer as<br>you wish</li>
      <li class="care__step">5. Style as desired</li>
    </ol>
  </section>
</main>
</body>
</html>
```